Yacht, Boats, Watersports company needs a redesign of business card

Hello Designers!
We are a Boat dealership company that sells fun in the water, we sell boats, Yachts, Kayaks and also yacht WaterSport toys. We are looking to redesign our business cards in to something a little bit more sophisticated. in a way that we can make better use of our company colors. I'm attaching a zipped file containing the company 3 sets of company logo which one is an horizontal another one is a vertical and also a chromed 3d logo. Also is included two set of business cards that we use and also some designs that i think it's interesting. We use PMS 2026c Orange and PMS 7687C Blue. I would like to see at least two different options with the orange as accent and also using blue as an accent color. It's really important for the business cards to have a font option and size that is legible to most people. Our current website is wwww.coralpennant.com. Please visit if you want to have a better feeling of the Boat dealership
You can send Single sided or double side options. We are now using single sided but we may be open for a double side option if we really like the design.
Target Market(s)
Marine, boat sales, yacht sales, water toys sales/
Contact Information for Business Card
Name: Dale Whitcombe
Address: 212 North Fenwick Lane,
Seabright Cove, FL 33118
Phone: 954-731-8842
Fax: 954:731-8843
Cell: 954-382-1490
Email: dw@coralpennant.com
Website: coralpennant.com
Requirements
Must have
- the current information of the business card provided.
logo
use the PMS Colors
Nice to have
- a touch of elegance and sophistication but simple
Should not have
- should not have any typography that is hard to read, the card should be simple but yet sophisticated.

```html
<!DOCTYPE html>
<html lang="en">
<head>
<meta charset="utf-8">
<title>Coral Pennant Marine Center – Business Card</title>
<link rel="stylesheet" href="https://fonts.googleapis.com/css2?family=Oswald:wght@500&family=Poppins:wght@400;600&display=swap">
<style>
  :root {
    --backdrop: #2a2a2a;
    --paper: #ffffff;
    --brand-blue: #1f6db3;
    --brand-orange: #ee8a2a;
    --text-grey: #4a4a4a;
    --tint-blue: #e9f0f8;
    --back-blue: #2170b5;
    --back-mark: #46b8ee;
  }
  * { box-sizing: border-box; margin: 0; padding: 0; }
  html, body {
    width: 1125px; height: 1200px; overflow: hidden;
    background: var(--backdrop);
  }
  .card {
    position: absolute; left: 150px; width: 824px; height: 471px;
    overflow: hidden;
  }
  .card-front { top: 106px; background: var(--paper); }
  .card-back { top: 640px; background: var(--back-blue); }

  .front-tint {
    position: absolute; left: 385px; top: 40px; width: 440px; height: 440px;
    border-radius: 50%; background: var(--tint-blue); opacity: .55;
  }

  .brand {
    position: absolute; left: 40px; top: 42px; width: 330px;
    display: flex; flex-direction: column; align-items: center; gap: 18px;
  }
  .brand-dot {
    width: 90px; height: 90px; border-radius: 50%;
    background: var(--brand-orange);
  }
  .brand-name {
    font-family: "Poppins", sans-serif; font-weight: 600;
    font-size: 25px; letter-spacing: .5px; color: var(--brand-blue);
    text-transform: uppercase; white-space: nowrap;
  }

  .address {
    position: absolute; left: 40px; top: 252px;
    font-family: "Poppins", sans-serif; font-size: 18.5px; line-height: 23px;
    color: var(--text-grey);
  }
  .contact-list {
    position: absolute; left: 40px; top: 312px; list-style: none;
    font-family: "Poppins", sans-serif; font-size: 18.5px; line-height: 23.3px;
    color: var(--text-grey);
  }
  .contact-list li { display: flex; align-items: center; gap: 10px; }
  .contact-list svg { width: 16px; height: 16px; fill: var(--brand-blue); flex: none; }

  .holder-name {
    position: absolute; right: 47px; top: 318px;
    font-family: "Oswald", sans-serif; font-weight: 500; font-size: 41px;
    color: var(--brand-blue); text-transform: uppercase; letter-spacing: .3px;
  }

  .front-band { position: absolute; left: 0; bottom: 0; width: 100%; height: 15px; }

  .back-brand {
    position: absolute; left: 0; top: 112px; width: 100%;
    display: flex; flex-direction: column; align-items: center; gap: 34px;
  }
  .back-dot {
    width: 120px; height: 120px; border-radius: 50%;
    background: #1a5ea3;
  }
  .back-name {
    font-family: "Poppins", sans-serif; font-weight: 600; font-size: 33px;
    letter-spacing: .5px; color: var(--back-mark); text-transform: uppercase;
    white-space: nowrap;
  }
</style>
</head>
<body>

<section class="card card-front" aria-label="Card front">
  <div class="front-tint"></div>

  <div class="brand">
    <span class="brand-dot"></span>
    <span class="brand-name">Coral Pennant</span>
  </div>

  <p class="address">212 North Fenwick Lane<br>Seabright Cove, FL 33118</p>

  <ul class="contact-list">
    <li><svg viewBox="0 0 16 16" aria-hidden="true"><path d="M3.6 1.5l2.3 2.8-1.2 1.7c.9 2 2.3 3.4 4.3 4.3l1.7-1.2 2.8 2.3-1.2 2.3C7 13.7 2.3 9 1.3 2.7z"/></svg>954-731-8842</li>
    <li><svg viewBox="0 0 16 16" aria-hidden="true"><path d="M4.5 1h7a1 1 0 011 1v12a1 1 0 01-1 1h-7a1 1 0 01-1-1V2a1 1 0 011-1zm.6 2v9h5.8V3zM8 12.6a.8.8 0 100 1.6.8.8 0 000-1.6z"/></svg>954-382-1490</li>
    <li><svg viewBox="0 0 16 16" aria-hidden="true"><path d="M4 1h6l2 2v3H4zM1.5 7h13v6h-2v2h-9v-2h-2zm3.5 4v2.5h6V11z"/></svg>954:731-8843</li>
    <li><svg viewBox="0 0 16 16" aria-hidden="true"><path d="M1 3.5h14v9H1zm1.3 1.2v.4L8 9l5.7-3.9v-.4z"/></svg>dw@coralpennant.com</li>
    <li><svg viewBox="0 0 16 16" aria-hidden="true"><path d="M8 1a7 7 0 100 14A7 7 0 008 1zm-1 2.3c-.5 1.2-2.2 1.5-2 3 .3 1.6 2.3 1 2.6 2.6.2 1.2-.6 2.3-.2 3.6A5.3 5.3 0 017 3.3zm3.5 1.3c.9.7 2.5 2.1 2 3.6-.6-.5-1.6-.6-2.1-1.4-.4-.7.3-1.4.1-2.2z"/></svg>coralpennant.com</li>
  </ul>

  <h1 class="holder-name">Dale Whitcombe</h1>

  <svg class="front-band" viewBox="0 0 824 15" preserveAspectRatio="none" aria-hidden="true">
    <polygon points="0,0 505,0 500,15 0,15" fill="var(--brand-blue)"/>
    <polygon points="510,0 824,0 824,15 505,15" fill="var(--brand-orange)"/>
  </svg>
</section>

<section class="card card-back" aria-label="Card back">
  <div class="back-brand">
    <span class="back-dot"></span>
    <span class="back-name">Coral Pennant</span>
  </div>
</section>

</body>
</html>
```